Chimney Service company needs new business card design

We need a updated business card with our new logo added. We provide a full range of chimney services throughout Vermont and New Hampshire. The business card will be one sided and color. Attached is our current business card another document showing all the information we would like on the card.
We dont like a lot of flashy colors.... here is a link to our website to get an idea of our branding www.flueguardianvt.example

Target Market(s)

homeowners

Industry/Entity Type

Business

Contact Information for Business Card

See attached sheet for content.

Font styles to use
Serif
Sans Serif

Requirements
Must have
• all information provided on separate sheet
Should not have
• Additional information that may clogg up design

```html
<!DOCTYPE html>
<html lang="en">
<head>
<meta charset="utf-8">
<title>Flue Guardian – Business Card</title>
<link rel="stylesheet" href="https://fonts.googleapis.com/css2?family=Open+Sans:wght@400&display=swap">
<style>
  :root {
    --backdrop: #b9b9b9;
    --charcoal: #333333;
    --charcoal-deep: #2b2b2b;
    --brick-red: #8b0306;
    --paper: #ececec;
    --silver: #dedede;
    --ink: #3a3a3a;
    --white: #ffffff;
  }
  * { margin: 0; padding: 0; box-sizing: border-box; }
  html, body { width: 1200px; height: 576px; overflow: hidden; }
  body { background: var(--backdrop); position: relative; font-family: "Open Sans", sans-serif; }

  .card {
    position: absolute;
    top: 138px;
    width: 484px;
    height: 292px;
    border-radius: 14px;
    overflow: hidden;
  }

  /* Front */
  .card-front { left: 82px; background: var(--charcoal); }
  .front-name {
    position: absolute; left: 0; right: 0; top: 146px;
    transform: translateY(-50%);
    text-align: center;
    font-size: 26px; font-weight: 400; letter-spacing: 1.5px;
    color: var(--silver);
  }

  /* Back */
  .card-back { left: 602px; background: var(--paper); }
  .back-shape { position: absolute; inset: 0; }

  .services {
    position: absolute; left: 24px; top: 32px; list-style: none;
    color: var(--white); font-size: 12.2px; line-height: 16.4px;
  }
  .services li { display: flex; align-items: center; gap: 7px; }
  .services svg { width: 9px; height: 11px; fill: var(--white); flex: none; }

  .contact {
    position: absolute; left: 24px; top: 162px; list-style: none;
    color: var(--white); font-size: 12.2px; line-height: 19.5px;
  }
  .contact li { display: flex; align-items: center; gap: 10px; }
  .contact svg { width: 12px; height: 12px; fill: var(--white); flex: none; }

  .assurances {
    position: absolute; left: 24px; top: 236px; list-style: none;
    color: var(--white); font-size: 11.6px; line-height: 15.5px;
  }
  .assurances li::before { content: "»"; margin-right: 6px; }

  .back-name {
    position: absolute; left: 400px; top: 146px;
    transform: translate(-50%, -50%) rotate(-90deg);
    white-space: nowrap;
    font-size: 24px; font-weight: 400; letter-spacing: 1.5px;
    color: var(--ink);
  }
</style>
</head>
<body>

<section class="card card-front" aria-label="Card front">
  <div class="front-name">FLUE GUARDIAN</div>
</section>

<section class="card card-back" aria-label="Card back">
  <svg class="back-shape" viewBox="0 0 484 292" preserveAspectRatio="none">
    <path d="M0 0 H312 C282 70 266 150 280 215 C286 245 296 272 306 292 H0 Z" fill="var(--charcoal-deep)"/>
    <path d="M0 0 H304 C275 70 258 150 272 215 C278 245 288 272 298 292 H0 Z" fill="var(--brick-red)"/>
    <path d="M0 231 H268 C270 247 274 262 279 274 H0 Z" fill="var(--charcoal)"/>
  </svg>

  <ul class="services">
    <li><svg viewBox="0 0 10 12"><path d="M5 0C6 3 9 4 9 8A4 4 0 0 1 1 8C1 6 2 5 3 4C3 6 4 7 5 7C4 5 4 2 5 0Z"/></svg>Full Masonry Services</li>
    <li><svg viewBox="0 0 10 12"><path d="M5 0C6 3 9 4 9 8A4 4 0 0 1 1 8C1 6 2 5 3 4C3 6 4 7 5 7C4 5 4 2 5 0Z"/></svg>Historic chimney restoration</li>
    <li><svg viewBox="0 0 10 12"><path d="M5 0C6 3 9 4 9 8A4 4 0 0 1 1 8C1 6 2 5 3 4C3 6 4 7 5 7C4 5 4 2 5 0Z"/></svg>Stainless steel liners</li>
    <li><svg viewBox="0 0 10 12"><path d="M5 0C6 3 9 4 9 8A4 4 0 0 1 1 8C1 6 2 5 3 4C3 6 4 7 5 7C4 5 4 2 5 0Z"/></svg>New Chimney installations</li>
    <li><svg viewBox="0 0 10 12"><path d="M5 0C6 3 9 4 9 8A4 4 0 0 1 1 8C1 6 2 5 3 4C3 6 4 7 5 7C4 5 4 2 5 0Z"/></svg>Licensed &amp; Certified Chimney sweeps</li>
  </ul>

  <ul class="contact">
    <li><svg viewBox="0 0 12 12"><path d="M1 3C1 1 3 1 6 1S11 1 11 3V4H8V3H4V4H1Z M3 5H9L11 10V11H1V10Z"/></svg>802-555-0147</li>
    <li><svg viewBox="0 0 12 12"><path d="M0 2H12V10H0Z M1 3V3.5L6 7L11 3.5V3Z" fill-rule="evenodd"/></svg>info@flueguardianvt.example</li>
    <li><svg viewBox="0 0 12 12"><path d="M6 0A6 6 0 1 0 6 12A6 6 0 1 0 6 0Z M6 1.2C4.8 2.5 4.3 4 4.2 5.4H7.8C7.7 4 7.2 2.5 6 1.2Z M1.2 5.4H3.3C3.4 4 3.8 2.6 4.6 1.4A4.9 4.9 0 0 0 1.2 5.4Z M8.7 5.4H10.8A4.9 4.9 0 0 0 7.4 1.4C8.2 2.6 8.6 4 8.7 5.4Z M1.2 6.6A4.9 4.9 0 0 0 4.6 10.6C3.8 9.4 3.4 8 3.3 6.6Z M4.2 6.6C4.3 8 4.8 9.5 6 10.8C7.2 9.5 7.7 8 7.8 6.6Z M8.7 6.6C8.6 8 8.2 9.4 7.4 10.6A4.9 4.9 0 0 0 10.8 6.6Z" fill-rule="evenodd"/></svg>www.flueguardianvt.example</li>
  </ul>

  <ul class="assurances">
    <li>Fully Insured – Free Estimates</li>
    <li>Family Owned &amp; Operated</li>
  </ul>

  <div class="back-name">FLUE GUARDIAN</div>
</section>

</body>
</html>
```